Letterhead Design Project

I need letterhead designed for my law firm. It would also be used for web based stuff as well.

Industry/Entity Type

Law Firm

```html
<!DOCTYPE html>
<html lang="en">
<head>
<meta charset="utf-8">
<title>Harlow &amp; Wren Law Firm – Letterhead</title>
<link rel="stylesheet" href="https://fonts.googleapis.com/css2?family=Cinzel:wght@400;600&display=swap">
<style>
  :root {
    --backdrop: #e6e6e6;
    --paper: #ffffff;
    --strip-light: #cfcfcf;
    --strip-dark: #a9a9a9;
    --band: #283035;
    --accent: #3a8fd0;
    --ink: #3a3a3a;
    --band-text: #ffffff;
  }
  * { margin: 0; padding: 0; box-sizing: border-box; }
  html, body {
    width: 1200px;
    height: 848px;
    overflow: hidden;
    background: var(--backdrop);
  }
  .canvas {
    position: relative;
    width: 1200px;
    height: 848px;
  }
  .letterhead {
    position: absolute;
    left: 300px;
    top: 36px;
    width: 600px;
    height: 776px;
    background: var(--paper);
    box-shadow: 0 1px 4px rgba(0, 0, 0, 0.18);
    overflow: hidden;
  }
  .top-strip {
    position: absolute;
    left: 0; top: 0;
    width: 100%;
    height: 12px;
    background: var(--strip-light);
  }
  .accent-rule {
    position: absolute;
    left: 0;
    width: 100%;
    height: 2px;
    background: var(--accent);
  }
  .accent-rule--upper { top: 41px; }
  .accent-rule--lower { top: 77px; }
  .name-band {
    position: absolute;
    left: 0; top: 45px;
    width: 100%;
    height: 31px;
    background: var(--band);
    display: flex;
    align-items: center;
    justify-content: flex-end;
    padding-right: 20px;
  }
  .firm-name {
    font-family: 'Cinzel', serif;
    font-weight: 600;
    font-size: 12px;
    letter-spacing: 0.32em;
    color: var(--band-text);
    text-transform: uppercase;
    white-space: nowrap;
  }
  .contact {
    position: absolute;
    right: 20px;
    top: 88px;
    text-align: right;
    font-family: 'Cinzel', serif;
    font-size: 7.5px;
    line-height: 10px;
    color: var(--ink);
    letter-spacing: 0.04em;
    font-style: normal;
  }
  .footer-band {
    position: absolute;
    left: 0; bottom: 0;
    width: 100%;
    height: 37px;
    background: var(--strip-light);
  }
  .footer-rule {
    position: absolute;
    left: 0; top: 8px;
    width: 100%;
    height: 3px;
    background: var(--strip-dark);
  }
</style>
</head>
<body>
  <main class="canvas">
    <article class="letterhead">
      <div class="top-strip"></div>
      <div class="accent-rule accent-rule--upper"></div>
      <header class="name-band">
        <span class="firm-name">Harlow &amp; Wren Law Firm</span>
      </header>
      <div class="accent-rule accent-rule--lower"></div>
      <address class="contact">
        Company Address<br>
        Phone : 01234 567 89<br>
        Fax: 01234 567 89<br>
        www.yourcompanyname.com
      </address>
      <footer class="footer-band">
        <div class="footer-rule"></div>
      </footer>
    </article>
  </main>
</body>
</html>
```